RKT Building Advisors -Business card design request- Lioness black and white shema ONLY - No

It is a woman on construction company I would like the schema to be in black-and-white with the lioness and possibly a lion anulinus as me and my husband both kind of running I would like to see designs for both. Original art would be preferred but like I said I'm going to attach some pictures that I really like and also if you could check my website out that would be great.Please get very creative this is a very important company I will be combining quality construction services with quality construction company and community affiliates such as Halvery construction exedra I really need to show dominates all I'm really wanting is the black-and-white montre and the lioness image on the right side as you will see in some of the thumbnails from what I have had in the past it is OK but I can't connect with anything. These are the last of my advertising dollars I ask that you really please put some time and help me take my company it to the next century. This is going to be a global thing it will be very serious. I'm not trying to be arrogant I'm just trying to tell the truth I ask that you give me something of quality that something that I can put on folders billboards pains walking to places and that it's not that I'm a woman own business but I deftly want there to be A-line as and please play around with the image of the lion and lioness as my husband is a lot of the construction side and I have a decided if Im going to advertise that are notJmsconstructionmanagement.comJovanna Schlossenberg C.E.O.RKT Building Advisors Jovanna@jmsconstructionmanagement.com81.316.0990

Target Market(s)

Construction or management style. Understand theme ports of marketing and that this logo will be displayed on billboards D cows apps all across the country

Industry/Entity Type

Construction Company

Contact Information for Business Card

Marisela Quenderhart
C.E.O.

Marisela@rktbuildingadvisors.example

Www.rktbuildingadvisors.example

427.795.3318

If you can I would like my slogan on their connecting qualify construction services with qualified construction companies and community affiliates

Font styles to use
Sans Serif

Colors
ffffff

Requirements
Must have
• Black-and-white schema lioness on the back side I will list my services will get to that but for now I wanna get the logo design I very open to where you maneuver the contact information
• Marisela Quenderhart
• C.E.O.
• Marisela@rktbuildingadvisors.example
• Www.rktbuildingadvisors.example
• 427.795.3318
• If you can I would like my slogan on their connecting qualified construction services with qualified construction companies and community affiliates
Nice to have
• Everything I mentioned above.
• I have added a few pictures with a lion and Linus and know this may seem crazy but I do not like that they are facing to the left I would rather the lion and lioness looked to the right and face forward. Also all the images need to be in black-and-white have provided some color want but I'd like them change to sepia .
Should not have
• I do not want it to look like a cartoon I need this to be of the utmost professionalism

```html
<!DOCTYPE html>
<html lang="en">
<head>
<meta charset="UTF-8">
<title>RKT Building Advisors – Business Card</title>
<link href="https://fonts.googleapis.com/css2?family=Montserrat:wght@600&family=Roboto:wght@400;500&display=swap" rel="stylesheet">
<style>
  :root {
    --backdrop: #7a5c3c;
    --card-light: #ffffff;
    --card-dark: #050505;
    --ink: #111111;
    --ink-soft: #1c1c1c;
    --paper-text: #ffffff;
    --mark-light: #d6d6d6;
    --mark-dark: #1f1f1f;
  }
  * { margin: 0; padding: 0; box-sizing: border-box; }
  html, body { width: 900px; height: 1200px; overflow: hidden; }
  body { background: var(--backdrop); position: relative; font-family: "Roboto", Arial, sans-serif; }

  .card {
    position: absolute;
    left: 120px;
    width: 659px;
    height: 385px;
    overflow: hidden;
    box-shadow: 0 6px 18px rgba(0,0,0,0.45);
  }
  .card--front { top: 178px; background: var(--card-light); color: var(--ink); }
  .card--back { top: 655px; background: var(--card-dark); color: var(--paper-text); }

  .watermark { position: absolute; }
  .card--front .watermark--head {
    left: -10px; top: 10px; width: 220px; height: 375px;
    background: radial-gradient(ellipse at 45% 45%, var(--mark-light) 0%, rgba(214,214,214,0.55) 45%, rgba(255,255,255,0) 72%);
  }
  .card--back .watermark--left {
    left: -20px; top: 0; width: 260px; height: 385px;
    background: radial-gradient(ellipse at 45% 45%, var(--mark-dark) 0%, rgba(31,31,31,0.5) 50%, rgba(5,5,5,0) 75%);
  }
  .card--back .watermark--right {
    right: -20px; top: 0; width: 300px; height: 385px;
    background: radial-gradient(ellipse at 55% 45%, var(--mark-dark) 0%, rgba(31,31,31,0.5) 50%, rgba(5,5,5,0) 75%);
  }

  .brand-dot {
    position: absolute; left: 50%; border-radius: 50%;
    transform: translateX(-50%);
  }
  .card--front .brand-dot { top: 44px; width: 60px; height: 60px; background: var(--ink); }
  .card--back .brand-dot { top: 104px; width: 80px; height: 80px; background: var(--paper-text); }

  .brand-name {
    position: absolute; left: 0; right: 0; text-align: center;
    font-family: "Montserrat", Arial, sans-serif; font-weight: 600;
    text-transform: uppercase; line-height: 1;
  }
  .card--front .brand-name { top: 142px; font-size: 28px; line-height: 32px; }
  .card--back .brand-name { top: 220px; font-size: 30px; line-height: 37px; }

  .tagline {
    position: absolute; left: 0; right: 0; top: 206px;
    text-align: center; font-size: 16px; color: var(--ink-soft);
  }

  .person { position: absolute; left: 46px; top: 252px; }
  .person__name { font-size: 16px; font-weight: 500; line-height: 20px; }
  .person__title { font-size: 14px; line-height: 20px; }

  .contacts {
    position: absolute; right: 44px; top: 250px;
    list-style: none; text-align: right;
  }
  .contacts li {
    display: flex; justify-content: flex-end; align-items: center;
    font-size: 14px; height: 20.5px; gap: 9px;
  }
  .contacts svg { width: 13px; height: 13px; fill: var(--ink); flex: none; }

  .slogan {
    position: absolute; left: 0; right: 0; top: 319px;
    text-align: center; font-size: 16px; line-height: 20px; color: var(--paper-text);
  }
</style>
</head>
<body>

<section class="card card--front" aria-label="Business card front">
  <div class="watermark watermark--head" role="img" aria-label="Large faint grey brand emblem decoration"></div>
  <div class="brand-dot"></div>
  <h1 class="brand-name">RKT Building<br>Advisors</h1>
  <p class="tagline">Loyal • Honest • Prosperous • Strong</p>

  <div class="person">
    <p class="person__name">Marisela Quenderhart</p>
    <p class="person__title">C.E.O.</p>
  </div>

  <ul class="contacts">
    <li>427.795.3318
      <svg viewBox="0 0 16 16"><path d="M3.5 1l2.5 3-1.5 1.8c.9 2 2.6 3.8 4.7 4.7L11 9l3 2.5-1.4 2.6c-5.5-.6-10.1-5.2-10.7-10.7z"/></svg></li>
    <li>427.795.3372
      <svg viewBox="0 0 16 16"><path d="M4 0h8a1 1 0 0 1 1 1v14a1 1 0 0 1-1 1H4a1 1 0 0 1-1-1V1a1 1 0 0 1 1-1zm1 2v10h6V2zm3 11a1 1 0 1 0 0 2 1 1 0 0 0 0-2z"/></svg></li>
    <li>427.795.3390
      <svg viewBox="0 0 16 16"><path d="M4 1h8v4H4zM1 6h14v6h-3v3H4v-3H1zm4 4v4h6v-4z"/></svg></li>
    <li>Marisela@rktbuildingadvisors.example
      <svg viewBox="0 0 16 16"><path d="M1 3h14v10H1zm1.5 1.2L8 8.5l5.5-4.3z"/></svg></li>
    <li>www.rktbuildingadvisors.example
      <svg viewBox="0 0 16 16" fill="none"><g fill="none" stroke="#111" stroke-width="1.3"><circle cx="8" cy="8" r="6.5"/><ellipse cx="8" cy="8" rx="3" ry="6.5"/><path d="M1.5 8h13M2.5 4.8h11M2.5 11.2h11"/></g></svg></li>
  </ul>
</section>

<section class="card card--back" aria-label="Business card back">
  <div class="watermark watermark--left" role="img" aria-label="Faint dark brand emblem decoration"></div>
  <div class="watermark watermark--right" role="img" aria-label="Faint dark brand emblem decoration"></div>
  <div class="brand-dot"></div>
  <h2 class="brand-name">RKT Building<br>Advisors</h2>
  <p class="slogan">Connecting Qualified Construction Services with Qualified Construction Companies<br>and Community Affiliates</p>
</section>

</body>
</html>
```